Business Card Design

Attached is my current Business card I do not like it but I must save the logo portion of it. Don't like the color or the lettering am looking for more architectural look in grays or taupe with the green more of a charturese color and the blue a charcoal color on a textured paper that looks more like something high-end that would appeal to an architect or a designer. We make concrete decorative items such as concrete fireplaces, sinks, tops and more.

Target Market(s)

Architects designers of Commercial and Residential - artistic features

Industry/Entity Type

Architect

Contact Information for Business Card

Marisol T. Quenby President and Marketing Director
602-418-5093
email marisol@vantorelstone.example
Showroom "Quillmont Design Center" 4183 W Palomar Scottsdale AZ
Fax: 602-731-6624

Font styles to use
Sans Serif

Requirements
Must have
• Architectural
Natural and earthy colors with a touch of color in the existing attached

```html
<!DOCTYPE html>
<html lang="en">
<head>
<meta charset="utf-8">
<title>Vantorel Stone Design Studio — Business Card</title>
<link rel="stylesheet" href="https://fonts.googleapis.com/css2?family=Saira:wght@300;400;500&display=swap">
<style>
  :root {
    --backdrop: #6c7476;
    --paper: #f1f1ee;
    --charcoal: #5d6567;
    --chartreuse: #9dc43a;
    --shadow: rgba(30, 36, 38, 0.35);
  }
  * { box-sizing: border-box; margin: 0; padding: 0; }
  html, body {
    width: 1200px;
    height: 1042px;
    overflow: hidden;
    background: var(--backdrop);
    font-family: "Saira", sans-serif;
    color: var(--charcoal);
  }
  .canvas {
    position: relative;
    width: 1200px;
    height: 1042px;
  }
  .card {
    position: absolute;
    left: 200px;
    width: 800px;
    height: 457px;
    background: var(--paper);
    box-shadow: 0 10px 28px var(--shadow);
  }
  .card--front { top: 48px; }
  .card--back { top: 545px; }

  /* Front */
  .brand {
    position: absolute;
    left: 0;
    right: 0;
    top: 150px;
    text-align: center;
  }
  .brand__row {
    display: flex;
    align-items: center;
    justify-content: center;
    gap: 18px;
  }
  .brand__square {
    width: 34px;
    height: 34px;
    background: var(--chartreuse);
  }
  .brand__name {
    font-size: 64px;
    font-weight: 400;
    line-height: 1;
    color: var(--charcoal);
  }
  .brand__tagline {
    margin-top: 14px;
    font-size: 26px;
    font-weight: 400;
    letter-spacing: 0.22em;
    color: var(--charcoal);
  }

  /* Back */
  .back-mark {
    position: absolute;
    left: 0;
    right: 0;
    top: 92px;
    display: flex;
    align-items: center;
    justify-content: center;
    gap: 12px;
  }
  .back-mark__square {
    width: 22px;
    height: 22px;
    background: var(--chartreuse);
  }
  .back-mark__name {
    font-size: 38px;
    font-weight: 400;
    color: var(--charcoal);
    line-height: 1;
  }
  .person {
    position: absolute;
    left: 0;
    right: 0;
    top: 205px;
    text-align: center;
  }
  .person__name {
    font-size: 36px;
    font-weight: 400;
    letter-spacing: 0.04em;
    line-height: 1.1;
  }
  .person__title {
    font-size: 15px;
    font-weight: 400;
    letter-spacing: 0.06em;
    margin-top: 2px;
  }
  .contact {
    position: absolute;
    bottom: 46px;
    font-size: 15px;
    font-weight: 400;
    line-height: 1.5;
  }
  .contact--direct { left: 34px; }
  .contact--showroom { right: 34px; text-align: right; }
  .contact__gap { margin-left: 10px; }
</style>
</head>
<body>
  <main class="canvas">
    <section class="card card--front" aria-label="Card front">
      <div class="brand">
        <div class="brand__row">
          <span class="brand__square" aria-hidden="true"></span>
          <span class="brand__name">Vantorel Stone</span>
        </div>
        <p class="brand__tagline">Design Studio</p>
      </div>
    </section>

    <section class="card card--back" aria-label="Card back">
      <div class="back-mark">
        <span class="back-mark__square" aria-hidden="true"></span>
        <span class="back-mark__name">Vantorel Stone</span>
      </div>
      <div class="person">
        <h1 class="person__name">Marisol T. Quenby</h1>
        <p class="person__title">President and Marketing Director</p>
      </div>
      <address class="contact contact--direct" style="font-style:normal">
        <p>Call 602-418-5093<span class="contact__gap">Fax 602-731-6624</span></p>
        <p>marisol@vantorelstone.example</p>
      </address>
      <address class="contact contact--showroom" style="font-style:normal">
        <p>Showroom “Quillmont Design Center”</p>
        <p>4183 W Palomar, Scottsdale, AZ</p>
      </address>
    </section>
  </main>
</body>
</html>
```